Web design for financial services

A modern web design of financial services (brokerage firm)
Req.s and technology tags :
- Very mobile friendly.
- One paged with some inner pages.
- Animated sticky header .
- Member login area for e-trade.
- Support RTL language.
- HTML & CSS.

The logo will be Home link
• MPTR :
WHO WE ARE
Content :
i) Board of Directors
ii) Mission Statement
iii) Corporate Values
iv) Regulations
• Financial Services :
WHAT WE DO
Content:
i) Electronic trading
ii) Trading desk
iii) Institutional
iv) Investors Education
• News
• Market Tools
• Forms---- opens new page
• Careers---- opens new page
• Contact Us----opens new page

The website is :
http://www.mptr-doha-example.com/

The logo need some changes to be more modern and impressively , but with keeping same structure .

Some related websites :
https://www.lv-bourse.example/

financial market

Financial Service

Coded - Design and coding required

2 page

• same fonts of http://www.kwdholdings.example/

• - Very mobile friendly.
• - One paged with some inner pages.
• - Animated sticky header .
• - Member login area for e-trade.
• - Support RTL language.
• - HTML & CSS.
• Slider , some Qatari theme,
• i like the video inside the home page
• ex :http://www.kwdholdings.example/

```html
<!DOCTYPE html>
<html lang="en">
<head>
<meta charset="utf-8">
<title>MPTR – Financial Services</title>
<link rel="stylesheet" href="https://fonts.googleapis.com/css2?family=Open+Sans:wght@300;400;600;700&display=swap">
<style>
  :root {
    --brand-red: #b3282b;
    --brand-red-dark: #8e1f22;
    --heading-red: #8a1c1e;
    --ink: #333333;
    --muted: #858585;
    --panel: #f7f7f7;
    --footer: #3b3b3b;
    --white: #ffffff;
  }
  * { box-sizing: border-box; margin: 0; padding: 0; }
  html, body { width: 1200px; height: 2500px; overflow: hidden; }
  body { position: relative; background: var(--white); font-family: "Open Sans", Arial, sans-serif; color: var(--ink); }

  /* Header */
  .site-header { position: absolute; top: 0; left: 0; width: 1200px; height: 117px; border-top: 3px solid var(--brand-red-dark); background: var(--white); box-shadow: 0 1px 3px rgba(0,0,0,.08); z-index: 2; }
  .brand { position: absolute; left: 133px; top: 24px; display: flex; align-items: center; gap: 12px; text-decoration: none; }
  .brand-mark { width: 30px; height: 30px; border-radius: 50%; background: var(--brand-red); }
  .brand-name { font-size: 30px; font-weight: 700; color: var(--ink); letter-spacing: 1px; }
  .utility { position: absolute; top: 26px; right: 133px; display: flex; align-items: center; gap: 14px; }
  .flag { width: 14px; height: 9px; background: linear-gradient(#c8102e 0 33%, #fff 33% 66%, #1f3c88 66%); }
  .btn-login { width: 73px; height: 23px; background: var(--brand-red); color: var(--white); font-size: 10px; display: flex; align-items: center; justify-content: center; border-radius: 2px; }
  .lang { font-size: 10px; color: var(--ink); display: flex; align-items: center; gap: 8px; }
  .lang svg { width: 7px; height: 5px; }
  .main-nav { position: absolute; right: 133px; top: 70px; display: flex; }
  .main-nav a { display: block; padding: 9px 16px 0; height: 44px; font-size: 11px; color: var(--ink); text-decoration: none; letter-spacing: .2px; }
  .main-nav a:last-child { padding-right: 0; }
  .main-nav a.active { color: var(--brand-red); border-bottom: 3px solid var(--brand-red); }

  /* Hero */
  .hero { position: absolute; top: 117px; left: 0; width: 1200px; height: 473px; overflow: hidden;
    background:
      radial-gradient(ellipse 40% 35% at 8% 80%, rgba(70,90,220,.45), transparent 70%),
      radial-gradient(ellipse 30% 40% at 50% 70%, rgba(200,210,230,.22), transparent 70%),
      radial-gradient(ellipse 30% 35% at 92% 75%, rgba(110,60,210,.5), transparent 70%),
      radial-gradient(ellipse 60% 20% at 50% 100%, rgba(210,140,60,.45), transparent 75%),
      linear-gradient(180deg, #1d1c22 0%, #25232f 40%, #2c2846 70%, #3a2f45 100%); }
  .hero-play { position: absolute; left: 584px; top: 160px; width: 32px; height: 32px; }
  .hero-title { position: absolute; top: 205px; width: 100%; text-align: center; font-size: 48px; font-weight: 300; color: var(--white); }
  .hero-cta { position: absolute; left: 522px; top: 293px; width: 156px; height: 50px; background: var(--brand-red); color: var(--white); font-size: 14px; display: flex; align-items: center; justify-content: center; border-radius: 2px; box-shadow: 0 1px 3px rgba(0,0,0,.35); }
  .hero-dots { position: absolute; top: 428px; left: 579px; display: flex; gap: 9px; }
  .hero-dots span { width: 9px; height: 9px; border-radius: 50%; background: rgba(255,255,255,.5); }
  .hero-dots span.on { background: var(--white); }

  /* Intro blocks */
  .feature { position: absolute; left: 133px; width: 934px; height: 280px; }
  .feature-media { position: absolute; top: 0; width: 336px; height: 280px; }
  .feature-copy { position: absolute; top: 0; width: 555px; }
  .section-title { font-size: 34px; font-weight: 400; color: var(--heading-red); line-height: 1; }
  .feature-copy p { margin-top: 23px; font-size: 10.5px; line-height: 24px; color: var(--muted); text-align: justify; }
  .feature-copy .section-title + p { margin-top: 20px; }
  .btn-small { display: inline-flex; align-items: center; justify-content: center; height: 38px; padding: 0 20px; margin-top: 24px; background: var(--brand-red); color: var(--white); font-size: 11px; border-radius: 2px; box-shadow: 0 1px 2px rgba(0,0,0,.25); }
  .who-we-are { top: 660px; }
  .who-we-are .feature-media { left: 0;
    background:
      radial-gradient(ellipse 45% 55% at 50% 35%, rgba(40,55,80,.55), transparent 70%),
      linear-gradient(180deg, #c9d9ec 0%, #a8bcd3 45%, #e8eef5 75%, #cbd5e0 100%); }
  .who-we-are .feature-copy { left: 380px; }
  .what-we-do { top: 1033px; }
  .what-we-do .feature-media { right: 0;
    background:
      radial-gradient(ellipse 35% 60% at 35% 45%, rgba(70,85,110,.55), transparent 70%),
      radial-gradient(ellipse 40% 60% at 90% 70%, rgba(110,150,190,.5), transparent 70%),
      linear-gradient(120deg, #eef1ea 0%, #e4ebea 40%, #bccbd9 75%, #8fa9c4 100%); }
  .what-we-do .feature-copy { left: 0; top: 3px; }

  /* News */
  .news { position: absolute; top: 1398px; left: 0; width: 1200px; height: 492px; background: var(--panel); }
  .centered-title { position: absolute; width: 100%; text-align: center; }
  .news .centered-title { top: 66px; }
  .card { position: absolute; width: 292px; }
  .card-media { width: 292px; height: 152px; }
  .card h3 { margin-top: 30px; font-size: 18px; font-weight: 400; color: var(--heading-red); }
  .card p { margin-top: 14px; font-size: 10.5px; line-height: 24px; color: var(--muted); }
  .news .card { top: 147px; }

  /* Partners */
  .partners { position: absolute; top: 1890px; left: 0; width: 1200px; height: 160px; }
  .partners .arrow { position: absolute; top: 58px; width: 24px; height: 46px; }
  .partners .arrow.prev { left: 138px; }
  .partners .arrow.next { right: 138px; }
  .partner-list { position: absolute; top: 66px; left: 210px; width: 780px; display: flex; justify-content: space-around; align-items: center; }
  .partner-name { font-size: 19px; font-weight: 400; color: #5a5a5a; }

  /* Market tools */
  .market-tool .centered-title { top: 2066px; }
  .market-tool .card { top: 2146px; }
  .market-tool .card-media { height: 140px; }
  .market-tool .card h3 { margin-top: 24px; text-align: center; }

  /* Footer */
  .site-footer { position: absolute; top: 2392px; left: 0; width: 1200px; height: 108px; background: var(--footer); }
  .social { position: absolute; top: 25px; left: 553px; display: flex; gap: 9px; }
  .social span { width: 26px; height: 26px; border-radius: 50%; background: #d9d9d9; border: 2px solid #bdbdbd; }
  .copyright { position: absolute; top: 69px; width: 100%; text-align: center; font-size: 10px; color: #cfcfcf; }
</style>
</head>
<body>

<header class="site-header">
  <a class="brand" href="#"><span class="brand-mark"></span><span class="brand-name">MPTR</span></a>
  <div class="utility">
    <span class="flag"></span>
    <span class="btn-login">LOGIN</span>
    <span class="lang">ENGLISH <svg viewBox="0 0 7 5"><path d="M0 0h7L3.5 5z" fill="#333"/></svg></span>
  </div>
  <nav class="main-nav">
    <a class="active" href="#">MPTR</a>
    <a href="#">FINANCIAL SERVICE</a>
    <a href="#">NEWS</a>
    <a href="#">MARKET TOOL</a>
    <a href="#">FORMS</a>
    <a href="#">CAREERS</a>
  </nav>
</header>

<section class="hero" role="img" aria-label="Night skyline of Doha towers lit in blue, violet and gold">
  <svg class="hero-play" viewBox="0 0 32 32"><circle cx="16" cy="16" r="16" fill="rgba(255,255,255,.55)"/><path d="M12 9l11 7-11 7z" fill="#2a2a35"/></svg>
  <h1 class="hero-title">FINANCIAL SERVICES</h1>
  <span class="hero-cta">VIEW DETAILS</span>
  <div class="hero-dots"><span class="on"></span><span class="on"></span><span></span></div>
</section>

<section class="feature who-we-are">
  <div class="feature-media" role="img" aria-label="Business people in suits standing behind a meeting table"></div>
  <div class="feature-copy">
    <h2 class="section-title">WHO WE ARE</h2>
    <p>Meridian Pearl Trading Resources is a private Qatari company that aims to provide secure and technologically advanced methods of trading to its clients. Those facilities enables clients to trade faster, more secure &amp; private. Having this strategy in our in minds, with this online portal we begin.</p>
    <p>Meridian Pearl Trading Resources is a private Qatari company that aims to provide secure and technologically advanced methods of trading to its clients. Those facilities enables clients to trade faster, more secure &amp; private. Having this strategy in our in minds, with this online portal we begin.</p>
    <span class="btn-small">About MPTR</span>
  </div>
</section>

<section class="feature what-we-do">
  <div class="feature-copy">
    <h2 class="section-title">WHAT WE DO</h2>
    <p>Meridian Pearl Trading Resources is a private Qatari company that aims to provide secure and technologically advanced methods of trading to its clients. Those facilities enables clients to trade faster, more secure &amp; private. Having this strategy in our in minds, with this online portal we begin.</p>
    <p>Meridian Pearl Trading Resources is a private Qatari company that aims to provide secure and technologically advanced methods of trading to its clients. Those facilities enables clients to trade faster, more secure &amp; private. Having this strategy in our in minds, with this online portal we begin.</p>
    <span class="btn-small">Read More</span>
  </div>
  <div class="feature-media" role="img" aria-label="Businessman holding a tablet blended with a city skyline"></div>
</section>

<section class="news">
  <h2 class="section-title centered-title">NEWS</h2>
  <article class="card" style="left:133px">
    <div class="card-media" role="img" aria-label="Hands reviewing documents with a calculator" style="background:radial-gradient(ellipse 50% 60% at 35% 40%,rgba(120,110,100,.45),transparent 70%),linear-gradient(135deg,#f2f2f2,#c9c9c9 55%,#e6e6e6)"></div>
    <h3>FINANCIAL SERVICES</h3>
    <p>Lorem ipsum dolor sit amet, consectetur adipiscing elit, sed do eiusmod tempor incididunt ut labore</p>
  </article>
  <article class="card" style="left:453px">
    <div class="card-media" role="img" aria-label="Person working on a laptop beside printed charts" style="background:radial-gradient(ellipse 35% 50% at 60% 35%,rgba(50,50,55,.55),transparent 70%),linear-gradient(135deg,#f4f4f4,#d2d2d2 55%,#ececec)"></div>
    <h3>FINANCIAL SERVICES</h3>
    <p>Lorem ipsum dolor sit amet, consectetur adipiscing elit, sed do eiusmod tempor incididunt ut labore</p>
  </article>
  <article class="card" style="left:773px">
    <div class="card-media" role="img" aria-label="Tablet showing bar and pie charts on a desk" style="background:radial-gradient(ellipse 40% 55% at 55% 45%,rgba(90,120,210,.45),transparent 70%),linear-gradient(135deg,#eef3f7,#c7d6e4 55%,#dfe7ee)"></div>
    <h3>FINANCIAL SERVICES</h3>
    <p>Lorem ipsum dolor sit amet, consectetur adipiscing elit, sed do eiusmod tempor incididunt ut labore</p>
  </article>
</section>

<section class="partners">
  <svg class="arrow prev" viewBox="0 0 24 46"><path d="M22 2L2 23l20 21" fill="none" stroke="#cfcfcf" stroke-width="1.5"/></svg>
  <div class="partner-list">
    <span class="partner-name">Halvorsen</span>
    <span class="partner-name">Corvane Mobile</span>
    <span class="partner-name">Lumetta</span>
    <span class="partner-name">Brindle</span>
    <span class="partner-name">Oakfield</span>
  </div>
  <svg class="arrow next" viewBox="0 0 24 46"><path d="M2 2l20 21L2 44" fill="none" stroke="#cfcfcf" stroke-width="1.5"/></svg>
</section>

<section class="market-tool">
  <h2 class="section-title centered-title">MARKET TOOL</h2>
  <article class="card" style="left:133px">
    <div class="card-media" role="img" aria-label="Hand touching a rising bar chart display" style="background:radial-gradient(ellipse 40% 60% at 40% 40%,rgba(210,210,215,.5),transparent 70%),linear-gradient(135deg,#2b2f36,#6e767f 50%,#b9bec4)"></div>
    <h3>MOST ACTIVE COMPANY</h3>
  </article>
  <article class="card" style="left:453px">
    <div class="card-media" role="img" aria-label="Stock ticker board with green and blue price figures" style="background:radial-gradient(ellipse 45% 50% at 55% 55%,rgba(60,200,110,.55),transparent 70%),radial-gradient(ellipse 30% 50% at 95% 30%,rgba(230,170,60,.6),transparent 70%),linear-gradient(135deg,#0e2a5c,#1a5ea8 55%,#2a7fc0)"></div>
    <h3>TOP GAINER</h3>
  </article>
  <article class="card" style="left:773px">
    <div class="card-media" role="img" aria-label="Orange falling market chart on a dark screen" style="background:radial-gradient(ellipse 60% 45% at 50% 85%,rgba(235,150,40,.85),transparent 75%),linear-gradient(180deg,#141210,#2a2116 55%,#6a4216)"></div>
    <h3>TOP LOSER</h3>
  </article>
</section>

<footer class="site-footer">
  <div class="social"><span></span><span></span><span></span></div>
  <p class="copyright">© Copyrights 2017 - mptr-doha-example.com.</p>
</footer>

</body>
</html>
```